Company director needs a business card design

I am a semi-retired former senior finance executive who sits on a number of public and private company boards and do some consulting work. I work largely with emerging businesses but deal regularly with top end of town lawyers, bankers etc. I need a thoughtful but relatively conservative design which would also resonate with my younger client base. Some colour would be good. Information limited to name, address, office tel, mobile and email.

Finance

```html
<!DOCTYPE html>
<html lang="en">
<head>
<meta charset="utf-8">
<title>Adrian Vale – Business Card</title>
<link rel="stylesheet" href="https://fonts.googleapis.com/css2?family=Exo+2:wght@400;500;700&display=swap">
<style>
  :root {
    --stage: #e9e7e3;
    --card: #ffffff;
    --accent: #29a8e0;
    --ink: #1a1a1a;
    --ink-soft: #2b2b2b;
  }
  * { margin: 0; padding: 0; box-sizing: border-box; }
  html, body {
    width: 1200px;
    height: 800px;
    overflow: hidden;
    background: var(--stage);
    font-family: "Exo 2", "Segoe UI", sans-serif;
  }
  .card {
    position: absolute;
    left: 100px;
    top: 114px;
    width: 1000px;
    height: 572px;
    background: var(--card);
    box-shadow: 0 10px 30px rgba(0,0,0,0.12);
    overflow: hidden;
  }
  .contact {
    position: absolute;
    left: 150px;
    top: 92px;
    color: var(--ink-soft);
  }
  .contact__address {
    font-size: 23px;
    line-height: 1.15;
    letter-spacing: 0.5px;
    margin-bottom: 12px;
  }
  .contact__row {
    display: flex;
    align-items: center;
    gap: 14px;
    font-size: 21px;
    line-height: 1.45;
    letter-spacing: 0.5px;
  }
  .contact__icon {
    width: 20px;
    height: 20px;
    flex: none;
  }
  .band {
    position: absolute;
    left: 0;
    top: 286px;
    width: 580px;
    height: 46px;
    background: var(--accent);
  }
  .identity {
    position: absolute;
    left: 606px;
    top: 278px;
    text-align: right;
    color: var(--ink);
  }
  .identity__name {
    font-size: 36px;
    font-weight: 700;
    letter-spacing: 1px;
    line-height: 1;
    text-transform: uppercase;
  }
  .identity__role {
    font-size: 16px;
    font-weight: 500;
    margin-top: 2px;
  }
  .tab {
    position: absolute;
    right: 0;
    top: 352px;
    width: 150px;
    height: 44px;
    background: var(--accent);
  }
</style>
</head>
<body>
  <main class="card">
    <section class="contact">
      <p class="contact__address">Office Vale Inc 14 Elm Ave<br>Linford, NJ 07321</p>
      <p class="contact__row">
        <svg class="contact__icon" viewBox="0 0 20 20" aria-hidden="true">
          <rect x="2.5" y="2.5" width="15" height="15" rx="3" fill="none" stroke="var(--accent)" stroke-width="2.4"/>
        </svg>
        0047 2190 365
      </p>
      <p class="contact__row">
        <svg class="contact__icon" viewBox="0 0 20 20" aria-hidden="true">
          <rect x="4" y="2" width="12" height="16" fill="var(--accent)"/>
          <rect x="6" y="4" width="2" height="2" fill="#fff"/>
          <rect x="9" y="4" width="2" height="2" fill="#fff"/>
          <rect x="12" y="4" width="2" height="2" fill="#fff"/>
          <rect x="6" y="8" width="2" height="2" fill="#fff"/>
          <rect x="9" y="8" width="2" height="2" fill="#fff"/>
          <rect x="12" y="8" width="2" height="2" fill="#fff"/>
          <rect x="6" y="12" width="2" height="2" fill="#fff"/>
          <rect x="12" y="12" width="2" height="2" fill="#fff"/>
          <rect x="9" y="13" width="2" height="5" fill="#fff"/>
        </svg>
        0047 2190 588
      </p>
      <p class="contact__row">
        <svg class="contact__icon" viewBox="0 0 20 20" aria-hidden="true">
          <rect x="1" y="4" width="18" height="12" fill="var(--accent)"/>
          <path d="M1.5 4.5 L10 11 L18.5 4.5" fill="none" stroke="#fff" stroke-width="1.5"/>
        </svg>
        hello@avale.com
      </p>
    </section>

    <div class="band"></div>

    <section class="identity">
      <h1 class="identity__name">Adrian Vale</h1>
      <p class="identity__role">Managing Director</p>
    </section>

    <div class="tab"></div>
  </main>
</body>
</html>
```